Business Card Design

We are a residential half way house for the addict ,the alcoholic and dual diagnosed in recovery.
i house both men and woman age 18+

Industry/Entity Type

Residential

```html
<!DOCTYPE html>
<html lang="en">
<head>
<meta charset="utf-8">
<title>Harborlight Family Sober House – Business Card</title>
<link rel="stylesheet" href="https://fonts.googleapis.com/css2?family=Crimson+Pro:wght@400;500&display=swap">
<style>
  :root {
    --backdrop: #e7e2da;
    --card: #0b0b0c;
    --band-deep: #2f4fa6;
    --band-light: #3b93d3;
    --rule: #3553a8;
    --icon: #3a58b0;
    --text: #dcdcdc;
    --text-dark: #1c2a44;
    --art-a: #f3e9ff;
    --art-b: #8a4fd6;
    --art-c: #2a1f5a;
  }
  * { margin: 0; padding: 0; box-sizing: border-box; }
  html, body {
    width: 1200px; height: 892px; overflow: hidden;
    background: var(--backdrop);
    font-family: "Crimson Pro", "Times New Roman", serif;
  }
  .card {
    position: absolute; left: 100px; top: 156px;
    width: 1000px; height: 580px;
    background: var(--card);
    border-radius: 4px;
    box-shadow: 0 10px 30px rgba(0,0,0,.25);
    overflow: hidden;
    color: var(--text);
  }
  .card-shapes { position: absolute; inset: 0; }
  .artwork {
    position: absolute; left: 120px; top: 60px;
    width: 260px; height: 260px; border-radius: 50%;
    background: radial-gradient(circle at 40% 35%, var(--art-a) 0%, var(--art-b) 45%, var(--art-c) 100%);
  }
  .holder-name {
    position: absolute; left: 430px; top: 92px;
    font-size: 40px; font-weight: 500; color: #ffffff; letter-spacing: .5px;
  }
  .holder-role {
    position: absolute; left: 478px; top: 166px;
    font-size: 24px; color: var(--text-dark);
  }
  .company {
    position: absolute; left: 160px; top: 306px;
    font-size: 30px; letter-spacing: .6px; text-transform: uppercase;
  }
  .tagline {
    position: absolute; left: 178px; top: 352px; font-size: 27px;
  }
  .contact-line {
    position: absolute; left: 160px;
    display: flex; align-items: center; gap: 22px;
    font-size: 24px;
  }
  .contact-line.email { top: 430px; }
  .contact-line.address { top: 482px; }
  .contact-line svg { width: 24px; height: 24px; fill: var(--icon); }
  .phones {
    position: absolute; left: 690px; top: 370px;
    display: flex; flex-direction: column; gap: 14px;
  }
  .phone-row {
    display: flex; justify-content: space-between; align-items: center;
    width: 280px; font-size: 25px;
  }
  .phone-row svg { width: 24px; height: 24px; fill: var(--icon); }
</style>
</head>
<body>
  <main class="card">
    <svg class="card-shapes" viewBox="0 0 1000 580" aria-hidden="true">
      <polygon points="395,88 905,70 880,162 370,162" fill="var(--band-deep)"/>
      <polygon points="360,162 650,162 630,222 340,222" fill="var(--band-light)"/>
      <rect x="0" y="336" width="140" height="12" fill="var(--rule)"/>
      <rect x="730" y="330" width="270" height="2" fill="var(--rule)"/>
    </svg>

    <div class="artwork" role="img" aria-label="Colourful light-burst illustration of people celebrating"></div>

    <div class="holder-name">Marisol Vega</div>
    <div class="holder-role">Owner</div>

    <div class="company">Harborlight Family Sober House Inc</div>
    <div class="tagline">Your Sobriety is our Priority</div>

    <div class="contact-line email">
      <svg viewBox="0 0 24 24" aria-hidden="true"><path d="M2 5h20v14H2z M2 5l10 8 10-8" fill="var(--icon)"/><path d="M3 6l9 7 9-7" stroke="#0b0b0c" stroke-width="1.6" fill="none"/></svg>
      <span>marisolvega@mailbox.com</span>
    </div>
    <div class="contact-line address">
      <svg viewBox="0 0 24 24" aria-hidden="true"><path d="M12 2a7 7 0 0 0-7 7c0 5 7 13 7 13s7-8 7-13a7 7 0 0 0-7-7zm0 9.5a2.5 2.5 0 1 1 0-5 2.5 2.5 0 0 1 0 5z"/></svg>
      <span>2840 Palm Grove Rd. Lake Haven,Fla 33400</span>
    </div>

    <div class="phones">
      <div class="phone-row"><span>(555) 314-0271</span>
        <svg viewBox="0 0 24 24" aria-hidden="true"><path d="M6.6 10.8a15 15 0 0 0 6.6 6.6l2.2-2.2a1 1 0 0 1 1-.25 11 11 0 0 0 3.6.6 1 1 0 0 1 1 1V20a1 1 0 0 1-1 1A17 17 0 0 1 3 4a1 1 0 0 1 1-1h3.5a1 1 0 0 1 1 1 11 11 0 0 0 .6 3.6 1 1 0 0 1-.25 1z"/></svg></div>
      <div class="phone-row"><span>(555) 314-0272</span>
        <svg viewBox="0 0 24 24" aria-hidden="true"><path d="M6.6 10.8a15 15 0 0 0 6.6 6.6l2.2-2.2a1 1 0 0 1 1-.25 11 11 0 0 0 3.6.6 1 1 0 0 1 1 1V20a1 1 0 0 1-1 1A17 17 0 0 1 3 4a1 1 0 0 1 1-1h3.5a1 1 0 0 1 1 1 11 11 0 0 0 .6 3.6 1 1 0 0 1-.25 1z"/></svg></div>
      <div class="phone-row"><span>(555) 718-2049</span>
        <svg viewBox="0 0 24 24" aria-hidden="true"><path d="M7 3h10v5H7z M4 9h16v8h-3v4H7v-4H4z M9 14h6v5H9z"/></svg></div>
    </div>
  </main>
</body>
</html>
```